Local Roofing/Construction company business needs new biz card design

We need a new business card design, current cards are from the start of this operation and generic at best. We are a local Construction Company (General Contractor) with a majority of our work originating from insurance claims-exterior finish work is the main focus (Roofs-Siding-Gutters etc). Heavily involved with homeowners and the low ball offers they receive from insurance company's after a insurable event takes place. I have attached some of our original logo file(s) below.

```html
<!DOCTYPE html>
<html lang="en">
<head>
<meta charset="UTF-8">
<title>Stonegate Exteriors – Business Card</title>
<link href="https://fonts.googleapis.com/css2?family=Poppins:wght@400;500;700;800&display=swap" rel="stylesheet">
<style>
  :root {
    --backdrop: #e4e4e4;
    --card-white: #f7f7f7;
    --brand-green: #36d47b;
    --ink-dark: #0d1f22;
    --text: #1a1a1a;
  }
  * { box-sizing: border-box; margin: 0; padding: 0; }
  html, body { width: 1200px; height: 930px; overflow: hidden; }
  body {
    background: var(--backdrop);
    font-family: "Poppins", sans-serif;
    color: var(--text);
    position: relative;
  }
  .card {
    position: absolute;
    top: 316px;
    width: 525px;
    height: 300px;
    box-shadow: 0 6px 18px rgba(0,0,0,0.12);
  }
  .card--front { left: 50px; background: var(--card-white); }
  .card--back { left: 625px; background: var(--brand-green); display: flex; align-items: center; justify-content: center; }

  .brand {
    display: flex;
    align-items: center;
    gap: 14px;
  }
  .brand__mark {
    width: 30px; height: 30px;
    background: var(--brand-green);
  }
  .card--back .brand__mark { background: var(--ink-dark); }
  .brand__name {
    font-weight: 800;
    font-size: 30px;
    letter-spacing: 1px;
    color: var(--ink-dark);
    line-height: 1;
  }

  .card--front .brand {
    position: absolute;
    top: 58px;
    left: 0; right: 0;
    justify-content: center;
  }

  .person {
    position: absolute;
    top: 128px;
    left: 0; right: 0;
    text-align: center;
  }
  .person__name { font-weight: 700; font-size: 16px; letter-spacing: 0.5px; }
  .person__title { font-size: 10px; letter-spacing: 1px; margin-top: 1px; }

  .details {
    position: absolute;
    top: 190px;
    left: 0; right: 0;
    display: flex;
    justify-content: center;
    gap: 16px;
    font-size: 13px;
    line-height: 1.45;
  }
  .details__address { text-align: right; }
  .details__divider { width: 1px; background: var(--brand-green); }
  .contact { list-style: none; }
  .contact li { display: flex; align-items: center; gap: 7px; }
  .contact svg { width: 12px; height: 12px; flex: none; }
</style>
</head>
<body>
  <section class="card card--front">
    <div class="brand">
      <span class="brand__mark"></span>
      <span class="brand__name">STONEGATE EXTERIORS</span>
    </div>
    <div class="person">
      <p class="person__name">DANIEL MARSH</p>
      <p class="person__title">MANAGING DIRECTOR</p>
    </div>
    <div class="details">
      <address class="details__address" style="font-style:normal">
        18, Harrow Lane, Unit 4<br>30417, Westbrook
      </address>
      <span class="details__divider"></span>
      <ul class="contact">
        <li>
          <svg viewBox="0 0 24 24"><path fill="#1a1a1a" d="M6.6 10.8a15.1 15.1 0 0 0 6.6 6.6l2.2-2.2a1 1 0 0 1 1-.25 11.4 11.4 0 0 0 3.6.57 1 1 0 0 1 1 1V20a1 1 0 0 1-1 1A17 17 0 0 1 3 4a1 1 0 0 1 1-1h3.5a1 1 0 0 1 1 1c0 1.25.2 2.45.57 3.6a1 1 0 0 1-.25 1z"/></svg>
          044-555 210 384
        </li>
        <li>
          <svg viewBox="0 0 24 24"><rect x="2" y="5" width="20" height="14" fill="#1a1a1a"/><path d="M2 5l10 8 10-8" fill="none" stroke="#f7f7f7" stroke-width="1.6"/></svg>
          hello@stonegateext.com
        </li>
        <li>
          <svg viewBox="0 0 24 24"><circle cx="12" cy="12" r="10" fill="#1a1a1a"/><path d="M2 12h20M12 2c3 3 3 17 0 20M12 2c-3 3-3 17 0 20" fill="none" stroke="#f7f7f7" stroke-width="1.3"/></svg>
          www.stonegateext.com
        </li>
      </ul>
    </div>
  </section>

  <section class="card card--back">
    <div class="brand">
      <span class="brand__mark"></span>
      <span class="brand__name">STONEGATE EXTERIORS</span>
    </div>
  </section>
</body>
</html>
```